Business card - Harbor Crest Builders

Design a business card utilizing the given logo.
colors we like: Black, greys, Teal, blues.
Tri color card, horizontal orientation likely
Logo and name likely best on top.
Info on card:

Dennis Farrow
#8 - 4815 Alder Ridge Blvd.
Surrey, B.C. V3K 2R9

778.555.0193
dennisfarrow@tellmail.ca

Slogan: "Building Dreams"

We are a construction company that specializes in new home construction on the West coast of BC Canada. Open Concepts designs of high end homes.

```html
<!DOCTYPE html>
<html lang="en">
<head>
<meta charset="utf-8">
<title>Harbor Crest Builders – Business Card</title>
<link href="https://fonts.googleapis.com/css2?family=Orbitron:wght@500&family=Michroma&display=swap" rel="stylesheet">
<style>
  :root {
    --backdrop: #9c9c9c;
    --card: #f7f7f7;
    --ink: #1f1f1f;
    --band-black: #262626;
    --band-grey: #6e6e6e;
    --icon: #e9e9e9;
    --notch: #ffffff;
  }
  html, body {
    margin: 0;
    width: 1200px;
    height: 895px;
    overflow: hidden;
    background: var(--backdrop);
  }
  .stage {
    width: 1200px;
    height: 895px;
    display: flex;
    flex-direction: column;
    align-items: center;
    justify-content: center;
    gap: 44px;
  }
  .card { display: block; box-shadow: 0 6px 18px rgba(0,0,0,.25); }
  .card-face { fill: var(--card); }
  .band-black { fill: var(--band-black); }
  .band-grey { fill: var(--band-grey); }
  .notch { fill: none; stroke: var(--notch); stroke-width: 4; }
  .icon { fill: none; stroke: var(--icon); stroke-width: 2; }
  .icon-solid { fill: var(--icon); }
  .logo-dot { fill: var(--ink); }
  .logo-rule { stroke: var(--ink); stroke-width: 1.2; }
  .brand-name {
    font-family: "Orbitron", sans-serif;
    font-weight: 500;
    fill: var(--ink);
    letter-spacing: 1px;
  }
  .person-name {
    font-family: "Michroma", sans-serif;
    font-size: 17px;
    fill: var(--ink);
    letter-spacing: 1px;
  }
  .person-title {
    font-family: "Michroma", sans-serif;
    font-size: 8px;
    fill: var(--ink);
    letter-spacing: 1px;
  }
  .contact {
    font-family: "Michroma", sans-serif;
    font-size: 10.5px;
    fill: var(--ink);
  }
</style>
</head>
<body>
<main class="stage">

  <!-- Front: contact side -->
  <svg class="card card-front" width="620" height="354" viewBox="0 0 620 354">
    <rect class="card-face" width="620" height="354"/>

    <g class="brand-lockup">
      <circle class="logo-dot" cx="56" cy="66" r="22"/>
      <line class="logo-rule" x1="92" y1="44" x2="92" y2="88"/>
      <text class="brand-name" x="104" y="74" font-size="21">HARBOR CREST BUILDERS</text>
    </g>

    <g class="identity">
      <text class="person-name" x="596" y="108" text-anchor="end">DENNIS FARROW</text>
      <text class="person-title" x="596" y="124" text-anchor="end">GRAPHICS DESIGNER</text>
    </g>

    <g class="info-band">
      <rect class="band-grey" x="0" y="140" width="620" height="40"/>
      <polyline class="notch" points="200,138 212,160 200,182"/>
      <polyline class="notch" points="406,138 418,160 406,182"/>

      <g class="icon-globe" transform="translate(30 160)">
        <circle class="icon" r="10"/>
        <ellipse class="icon" rx="4.5" ry="10"/>
        <line class="icon" x1="-10" y1="0" x2="10" y2="0"/>
        <line class="icon" x1="-8.5" y1="-5" x2="8.5" y2="-5"/>
        <line class="icon" x1="-8.5" y1="5" x2="8.5" y2="5"/>
      </g>
      <g class="icon-pin" transform="translate(240 160)">
        <path class="icon-solid" d="M0 12 C-4 5 -8 1 -8 -4 A8 8 0 0 1 8 -4 C8 1 4 5 0 12 Z"/>
        <circle cx="0" cy="-4" r="3" fill="var(--band-grey)"/>
      </g>
      <g class="icon-phone" transform="translate(446 160)">
        <rect class="icon" x="-6.5" y="-11" width="13" height="22" rx="2"/>
        <line class="icon" x1="-2" y1="7" x2="2" y2="7"/>
      </g>
    </g>

    <g class="contact-web">
      <text class="contact" x="22" y="212">dennisfarrow@tellmail.ca</text>
      <text class="contact" x="22" y="232">www.harborcrestbuilders.ca</text>
    </g>
    <g class="contact-address">
      <text class="contact" x="228" y="212">#8 - 4815 Alder Ridge Blvd.</text>
      <text class="contact" x="228" y="232">Surrey, B.C. V3K 2R9</text>
    </g>
    <g class="contact-phone">
      <text class="contact" x="436" y="212">778.555.0193</text>
    </g>

    <g class="footer-band">
      <rect class="band-black" x="0" y="296" width="620" height="58"/>
    </g>
  </svg>

  <!-- Back: logo side -->
  <svg class="card card-back" width="620" height="354" viewBox="0 0 620 354">
    <rect class="card-face" width="620" height="354"/>

    <rect class="band-black" x="0" y="0" width="620" height="58"/>
    <polyline class="notch" points="292,0 310,22 292,44" transform="translate(0 14)"/>
    <rect class="band-black" x="0" y="296" width="620" height="58"/>
    <polyline class="notch" points="292,296 310,318 292,340"/>

    <g class="brand-lockup">
      <circle class="logo-dot" cx="96" cy="177" r="28"/>
      <line class="logo-rule" x1="140" y1="150" x2="140" y2="204"/>
      <text class="brand-name" x="154" y="187" font-size="26">HARBOR CREST BUILDERS</text>
    </g>
  </svg>

</main>
</body>
</html>
```